Membership Based Medical Practice Website

We need a functioning website for a new Membership based medical practice. There will be an enrollment fee and a monthly fee. We would like to see designs that are modern, simple. Should use neutral light colors. Examples of sites we like are www.kellanmoorclinic.com and https://fernholtcare.com/ We also have a link that when "Join Now" is clicked it will go to the signup website.

Target Market(s)

Gay Men, local population, Age group 20 to 60's.

Industry/Entity Type

Medical

Coding

Coded - Design and coding required

Number of Pages Required

5+ page

Font styles to use
Sans Serif

Colors
ffffff
cee9f5
ecf7fb
cfeae6
edf8f6
aaaaaa
e9e9e9
dbdbdb
fff3d1

Requirements
Must have
• Logo and header on every page. Clean, simple design, clear content, mobile compatible.
• Must use Wordpress
Nice to have
• Ideas should come from kellanmoorclinic.com
• Easy to read
Should not have
• Generic patient pictures, bold colors.
• Should not copy from above websites.

```html
<!DOCTYPE html>
<html lang="en">
<head>
<meta charset="utf-8">
<title>Corvale Aid — Specialty Medicine</title>
<link rel="stylesheet" href="https://fonts.googleapis.com/css2?family=Josefin+Sans:wght@300;400;600&family=Poppins:wght@400;500&family=Lato:wght@400;700&display=swap">
<style>
:root{
  --white:#ffffff;
  --sky:#cee9f5;
  --sky-light:#ecf7fb;
  --mint:#cfeae6;
  --mint-light:#edf8f6;
  --gray:#aaaaaa;
  --gray-light:#e9e9e9;
  --gray-mid:#dbdbdb;
  --cream:#fff3d1;
  --button:#7fc8ec;
  --ink:#1e1e1e;
  --text:#555555;
  --navy:#1d2b55;
  --gold:#d8a74c;
  --green:#2f9c7f;
}
*{box-sizing:border-box;margin:0;padding:0}
html,body{width:1200px;height:3529px;overflow:hidden}
body{position:relative;background:var(--white);font-family:"Josefin Sans",sans-serif;color:var(--ink)}
.abs{position:absolute}
.center{text-align:center}

/* header */
.site-header{left:0;top:0;width:1200px;height:125px;background:var(--white);z-index:3}
.brand{left:118px;top:0;width:245px;height:165px;background:var(--white);border-radius:0 0 50% 50%/0 0 40% 40%;z-index:4;display:flex;flex-direction:column;align-items:center;justify-content:flex-start;padding-top:34px}
.brand-dot{width:46px;height:46px;border-radius:50%;border:2px solid var(--gold)}
.brand-name{margin-top:14px;font-size:15px;letter-spacing:6px;color:var(--ink)}
.brand-sub{font-size:10px;letter-spacing:.5px;color:var(--ink);margin-top:2px}
.main-nav{left:497px;top:56px;width:484px;display:flex;justify-content:space-between;font-size:15px;letter-spacing:.6px;white-space:nowrap}
.btn{display:flex;align-items:center;justify-content:center;background:var(--button);color:var(--ink);font-size:16px;letter-spacing:1.5px;font-weight:600;box-shadow:0 4px 8px rgba(0,0,0,.15)}
.btn-join{left:1007px;top:45px;width:108px;height:37px;font-weight:400;font-size:15px}

/* hero */
.hero-image{left:0;top:125px;width:1200px;height:586px;background:linear-gradient(180deg,#a9b3b5 0%,#c6cccc 35%,#7e8d73 62%,#4a4f4a 100%)}
.hero-title{left:0;top:258px;width:1200px;font-size:41px;letter-spacing:5px;font-weight:400}
.hero-tagline{left:0;top:326px;width:1200px;font-size:20px;letter-spacing:.5px}
.btn-hero{left:532px;top:386px;width:136px;height:42px;background:var(--white);font-size:16px;font-weight:400;box-shadow:none}

/* services */
.intro{left:0;top:798px;width:1200px;font-size:25px;line-height:36px;color:var(--ink)}
.service-card{width:303px;height:270px;border-radius:14px;box-shadow:0 6px 14px rgba(0,0,0,.15);padding:0 30px}
.service-card h3{font-family:"Poppins",sans-serif;font-weight:500;font-size:31px;line-height:37px;text-align:center;height:110px;display:flex;align-items:center;justify-content:center;margin-top:24px}
.service-card p{font-family:"Lato",sans-serif;font-size:13px;line-height:17px;color:#8a8a8a;text-align:center;margin-top:20px}
.read-more{position:absolute;right:30px;bottom:22px;font-family:"Lato",sans-serif;font-size:10px;color:var(--navy);letter-spacing:.5px;font-weight:700}
.card-sky{background:var(--sky)}
.card-mint{background:var(--mint)}
.card-cream{background:var(--cream)}
.card-gray{background:var(--gray-light)}
.card-mint-light{background:var(--mint-light)}
.btn-view{left:513px;top:1617px;width:174px;height:42px}

/* features */
.subhead{left:0;top:1754px;width:1200px;font-size:27px;line-height:35px}
.feature{width:250px;text-align:center}
.feature svg{display:block;margin:0 auto}
.feature h4{font-size:15px;letter-spacing:1px;line-height:21px;font-weight:400;margin-top:18px}
.feature p{font-size:14px;line-height:21px;color:var(--text);margin-top:12px;padding:0 8px}

/* pricing */
.pricing-lead{left:0;top:2588px;width:1200px;font-size:25px}
.plan{left:0;top:2647px;width:1200px;font-size:33px;color:#555}
.plan strong{color:var(--green);font-weight:400}
.perks{left:118px;top:2742px;width:490px;list-style:none;font-size:20px;line-height:34.5px;color:#666}
.perks li{position:relative;padding-left:30px}
.perks li::before{content:"";position:absolute;left:0;top:9px;width:13px;height:13px;border-radius:50%;border:2px solid var(--gold)}
.photo-backing{left:675px;top:2751px;width:438px;height:247px;background:#9fd6c6}
.photo{left:656px;top:2732px;width:441px;height:249px;background:radial-gradient(circle at 50% 55%,#f2f2f2 0 22%,#27333d 23% 40%,#a52a2a 60%,#2b3238 100%)}
.btn-learn{left:470px;top:3104px;width:262px;height:42px}

/* footer */
.site-footer{left:0;top:3181px;width:1200px;height:348px;background:var(--cream);border-top-left-radius:340px 200px}
.footer-col{font-size:14px;color:var(--ink)}
.footer-col h5{font-size:13px;letter-spacing:2px;font-weight:400;margin-bottom:18px}
.footer-col a{display:block;color:#444;text-decoration:none;font-size:15px;line-height:29px}
.social{display:flex;gap:12px;margin-top:4px}
.social span{width:20px;height:20px;border-radius:50%;border:2px solid var(--ink)}
.subscribe{left:692px;top:3346px;width:440px;height:52px;display:flex;box-shadow:0 3px 8px rgba(0,0,0,.12)}
.subscribe .field{flex:0 0 242px;background:var(--white);display:flex;align-items:center;padding-left:20px;gap:16px;font-size:14px;color:#777}
.subscribe .submit{flex:1;background:var(--gray);color:var(--white);display:flex;align-items:center;justify-content:center;font-family:"Lato",sans-serif;font-weight:700;font-size:15px}
.copyright{left:0;top:3480px;width:1200px;font-size:13px;color:#666}
</style>
</head>
<body>

<header class="abs site-header">
  <nav class="abs main-nav"><span>HOME</span><span>SPECIALTIES</span><span>PRICING</span><span>ABOUT US</span><span>FAQ</span><span>BLOG</span></nav>
  <div class="abs btn btn-join">JOIN US</div>
</header>
<div class="abs brand">
  <div class="brand-dot"></div>
  <div class="brand-name">CORVALE</div>
  <div class="brand-sub">INFECTIOUS DISEASE SPECIALISTS</div>
</div>

<section>
  <div class="abs hero-image" role="img" aria-label="Misty valley with a long empty road stretching to the horizon"></div>
  <h1 class="abs hero-title center">CORVALE AID</h1>
  <p class="abs hero-tagline center">Specialty medicine with Commitment, Compassion and Care</p>
  <div class="abs btn btn-hero">JOIN US</div>
</section>

<section>
  <p class="abs intro center">We offer comprehensive treatment of a wide variety of infectious diseases.<br>Out expertise is in the following area.</p>

  <article class="abs service-card card-sky" style="left:130px;top:944px"><h3>HIV/PrEP</h3><p>Lorem ipsum dolor sit amet, consectetur adipiscing elit. Cras ullamcorper libero et tempus bibendum.</p><span class="read-more">READ MORE &nbsp;›</span></article>
  <article class="abs service-card card-mint" style="left:456px;top:944px"><h3>Chronic<br>Hepatitis</h3><p>Lorem ipsum dolor sit amet, consectetur adipiscing elit. Cras ullamcorper libero et tempus bibendum.</p><span class="read-more">READ MORE &nbsp;›</span></article>
  <article class="abs service-card card-cream" style="left:781px;top:944px"><h3>Bone &amp; Joint<br>Infections</h3><p>Lorem ipsum dolor sit amet, consectetur adipiscing elit. Cras ullamcorper libero et tempus bibendum.</p><span class="read-more">READ MORE &nbsp;›</span></article>
  <article class="abs service-card card-cream" style="left:130px;top:1273px"><h3>Tuberculosis</h3><p>Lorem ipsum dolor sit amet, consectetur adipiscing elit. Cras ullamcorper libero et tempus bibendum.</p><span class="read-more">READ MORE &nbsp;›</span></article>
  <article class="abs service-card card-gray" style="left:456px;top:1273px"><h3>Diabetes</h3><p>Lorem ipsum dolor sit amet, consectetur adipiscing elit. Cras ullamcorper libero et tempus bibendum.</p><span class="read-more">READ MORE &nbsp;›</span></article>
  <article class="abs service-card card-mint-light" style="left:781px;top:1273px"><h3>Postsurgical</h3><p>Lorem ipsum dolor sit amet, consectetur adipiscing elit. Cras ullamcorper libero et tempus bibendum.</p><span class="read-more">READ MORE &nbsp;›</span></article>

  <div class="abs btn btn-view">VIEW MORE</div>
</section>

<section>
  <p class="abs subhead center">Less wait, more personal.<br>We are not your traditional doctor’s office.</p>

  <div class="abs feature" style="left:73px;top:1915px">
    <svg width="90" height="90" viewBox="0 0 90 90" fill="none" stroke="#d8a74c" stroke-width="2.5"><circle cx="45" cy="45" r="26"/><path d="M53 35c-2-3-5-4-8-4-5 0-8 3-8 6 0 8 16 5 16 13 0 3-3 6-8 6-4 0-7-2-9-5M45 27v36"/></svg>
    <h4>STRAIGHTFORWARD<br>PRICING</h4><p>We charge all our patients the same low rate - no surprises.</p>
  </div>
  <div class="abs feature" style="left:346px;top:1915px">
    <svg width="90" height="90" viewBox="0 0 90 90" fill="none" stroke="#d8a74c" stroke-width="2.5"><rect x="22" y="25" width="46" height="42" rx="3"/><path d="M22 36h46M32 20v10M58 20v10M31 45h6M42 45h6M53 45h6M31 55h6M42 55h6M53 55h6"/></svg>
    <h4>AVAILABLE WHEN<br>YOU ARE</h4><p>New patient appointments are available within 1 week</p>
  </div>
  <div class="abs feature" style="left:621px;top:1915px">
    <svg width="90" height="90" viewBox="0 0 90 90" fill="none" stroke="#d8a74c" stroke-width="2.5"><circle cx="45" cy="45" r="24"/><path d="M45 30v15l10 7"/></svg>
    <h4>HASSLE-FREE<br>BOOKING</h4><p>Schedule your appointment online at your convenience - no need to call during business</p>
  </div>
  <div class="abs feature" style="left:892px;top:1915px">
    <svg width="90" height="90" viewBox="0 0 90 90" fill="none" stroke="#d8a74c" stroke-width="2.5"><path d="M16 40l12-10 12 6 10-6 12 4 12 8M28 30l-6 20 8 8M62 34l10 20-10 6M40 52l6 6 6-2 4 4"/></svg>
    <h4>DEVOTED<br>CARE</h4><p>We schedule enough time at each visit to make sure all of your questions are answered.</p>
  </div>

  <div class="abs feature" style="left:73px;top:2238px">
    <svg width="90" height="90" viewBox="0 0 90 90" fill="none" stroke="#d8a74c" stroke-width="2.5"><rect x="20" y="26" width="50" height="34" rx="3"/><path d="M38 66h14M45 60v6M30 36h14v10H36l-6 4zM50 40h10M50 46h10"/></svg>
    <h4>WITHIN YOUR<br>REACH</h4><p>Follow-up appointments may be done by video chat for your convenience.</p>
  </div>
  <div class="abs feature" style="left:346px;top:2238px">
    <svg width="90" height="90" viewBox="0 0 90 90" fill="none" stroke="#d8a74c" stroke-width="2.5"><path d="M56 22l12 12M52 30l8 8M58 28l-24 24-4 10 10-4 24-24M30 62l-6 6"/></svg>
    <h4>SAVE ON<br>LAB COSTS</h4><p>If paying upfront for labs, we offer discounted pricing of up to 90% off standard rates</p>
  </div>
  <div class="abs feature" style="left:621px;top:2238px">
    <svg width="90" height="90" viewBox="0 0 90 90" fill="none" stroke="#d8a74c" stroke-width="2.5"><rect x="28" y="28" width="28" height="38" rx="4"/><rect x="30" y="20" width="24" height="8" rx="2"/><path d="M42 40v14M35 47h14"/><rect x="56" y="52" width="18" height="9" rx="4.5"/></svg>
    <h4>SAVE ON<br>MEDICATIONS</h4><p>We offer deeply discounted wholesale prices medications for our members at pharmacy on site.</p>
  </div>
  <div class="abs feature" style="left:892px;top:2238px">
    <svg width="90" height="90" viewBox="0 0 90 90" fill="none" stroke="#d8a74c" stroke-width="2.5"><rect x="24" y="26" width="42" height="40" rx="4"/><path d="M34 26v-6h22v6M45 36v20M35 46h20"/></svg>
    <h4>NO MIDDLE<br>MAN</h4><p>We don’t bill any insurance plans so decisions about your healthcare will be made by you and Dr.</p>
  </div>
</section>

<section>
  <p class="abs pricing-lead center">Our pricing is simple, transparent and affordable.</p>
  <p class="abs plan center">Membership Plan <strong>$80/mo</strong>, plus a one-time <strong>$99</strong> enrollment fee.</p>
  <ul class="abs perks">
    <li>Includes all appointments, no co-pay</li>
    <li>Relaxed, unrushed visits</li>
    <li>Direct communication with your doctor via phone, email, video chat 24/7</li>
    <li>Convenient online scheduling (no need to call during business hours)</li>
    <li>Wholesale price for labs and medications</li>
  </ul>
  <div class="abs photo-backing"></div>
  <div class="abs photo" role="img" aria-label="Hands in red sleeves holding a white enamel camping mug outdoors"></div>
  <div class="abs btn btn-learn">LEARN MORE ABOUT US</div>
</section>

<footer class="abs site-footer">
  <div class="abs footer-col" style="left:132px;top:127px"><h5>LEARN MORE</h5><a>Contact Us</a><a>FAQs</a><a>Terms and Privacy</a></div>
  <div class="abs footer-col" style="left:318px;top:127px"><h5>OUR COMPANY</h5><a>Pricing</a><a>Team</a></div>
  <div class="abs footer-col" style="left:494px;top:127px"><h5>CONNECT WITH US</h5><div class="social" aria-label="Social links"><span></span><span></span><span></span></div></div>
  <div class="abs footer-col" style="left:692px;top:127px"><h5>SUBSCRIBE TO OUR NEWSLETTER</h5></div>
</footer>
<div class="abs subscribe">
  <div class="field"><svg width="20" height="16" viewBox="0 0 20 16" fill="none" stroke="#777" stroke-width="1.5"><rect x="1" y="1" width="18" height="14" rx="1.5"/><path d="M1 2l9 7 9-7"/></svg>Your email address</div>
  <div class="submit">Subscribe me now</div>
</div>
<p class="abs copyright center">corvaleaid.com © 2019. All Rights Reserved.</p>

</body>
</html>
```